Harborline Renewal Business Card Design

Professional and clean design. The design colors should flow with the logo. Two-sided card with the website on the back which is:

www.HarborlineRenewal.example.

"Specializing in Water Damage Restoration"

On the front I need the name, email, phone, and logo.

Name: Darnell Quisby
Email: Darnell@HarborlineRenewal.example
Phone: 555-318-2046 for now

I only have the Preview and Thumbnail right now but should have the source files uploaded within a day or two.

Target Market(s)

Flood victims, home owners with water damage from busted pipes etc...

Industry/Entity Type

Business

Contact Information for Business Card

Name: Darnell Quisby

Font styles to use
Serif
Sans Serif

Requirements
Must have
• Business Card Details Info

```html
<!DOCTYPE html>
<html lang="en">
<head>
<meta charset="UTF-8">
<title>Harborline Renewal – Business Card</title>
<link href="https://fonts.googleapis.com/css2?family=Open+Sans:ital,wght@0,400;0,600;1,700&display=swap" rel="stylesheet">
<style>
  :root {
    --page-bg: #e6e4e0;
    --card-frost-top: #f4f6f7;
    --card-frost-bottom: #e3e8eb;
    --band-deep: #0f4f8f;
    --band-mid: #2a7fc0;
    --band-light: #5eaee0;
    --swoosh-grey: #8d949b;
    --brand-navy: #1d4e86;
    --text-light: #eef3f7;
    --tagline-accent: #d2a77c;
  }
  * { margin: 0; padding: 0; box-sizing: border-box; }
  html, body {
    width: 1200px; height: 969px; overflow: hidden;
    background: var(--page-bg);
  }
  .card {
    position: absolute; left: 100px; top: 201px;
    width: 1000px; height: 566px;
    border-radius: 30px; overflow: hidden;
    background: linear-gradient(160deg, var(--card-frost-top), var(--card-frost-bottom));
    box-shadow: 0 18px 40px rgba(0,0,0,0.18);
    font-family: "Open Sans", Arial, sans-serif;
  }
  .card__band { position: absolute; inset: 0; }
  .brand {
    position: absolute; left: 540px; top: 60px; width: 420px;
    text-align: center; color: var(--brand-navy);
  }
  .brand__dot {
    display: block; width: 100px; height: 100px; margin: 0 auto 26px;
    border-radius: 50%; background: var(--brand-navy);
  }
  .brand__name {
    display: block; font-size: 38px; font-weight: 600;
    line-height: 1.2; white-space: nowrap;
  }
  .contact {
    position: absolute; left: 60px; top: 288px; color: var(--text-light);
  }
  .contact__name { font-size: 34px; font-weight: 600; margin-bottom: 20px; }
  .contact__row {
    display: flex; align-items: center; gap: 14px;
    font-size: 25px; line-height: 38px;
  }
  .contact__row svg { width: 24px; height: 24px; flex: none; fill: var(--text-light); }
  .tagline {
    margin-top: 12px; font-size: 25px; font-style: italic; font-weight: 700;
    color: var(--tagline-accent);
  }
  .tagline__lead { color: var(--text-light); }
</style>
</head>
<body>
  <div class="card">
    <svg class="card__band" width="1000" height="566" viewBox="0 0 1000 566" aria-hidden="true">
      <defs>
        <linearGradient id="bandFill" x1="0" y1="0" x2="1" y2="1">
          <stop offset="0" stop-color="var(--band-light)"/>
          <stop offset="0.5" stop-color="var(--band-mid)"/>
          <stop offset="1" stop-color="var(--band-deep)"/>
        </linearGradient>
      </defs>
      <path d="M0,0 H350 C330,200 520,450 770,566 H0 Z" fill="url(#bandFill)"/>
      <path d="M356,0 H410 C392,190 530,430 800,566 H782 C530,452 340,210 356,0 Z" fill="var(--swoosh-grey)" opacity="0.75"/>
    </svg>

    <div class="brand">
      <span class="brand__dot"></span>
      <span class="brand__name">Harborline Renewal</span>
    </div>

    <div class="contact">
      <p class="contact__name">Darnell Quisby</p>
      <p class="contact__row">
        <svg viewBox="0 0 24 24"><path d="M6.6 10.8a15.1 15.1 0 0 0 6.6 6.6l2.2-2.2a1 1 0 0 1 1-.25 11.4 11.4 0 0 0 3.6.57 1 1 0 0 1 1 1V20a1 1 0 0 1-1 1A17 17 0 0 1 3 4a1 1 0 0 1 1-1h3.5a1 1 0 0 1 1 1c0 1.25.2 2.45.57 3.57a1 1 0 0 1-.25 1z"/></svg>
        555-318-2046 for now
      </p>
      <p class="contact__row">
        <svg viewBox="0 0 24 24"><path d="M2 5h20v2l-10 6L2 7z"/><path d="M2 9l10 6 10-6v10H2z"/></svg>
        Darnell@HarborlineRenewal.example
      </p>
      <p class="contact__row">
        <svg viewBox="0 0 24 24"><circle cx="12" cy="12" r="10"/><path d="M12 2a10 10 0 0 0 0 20M2 12h20M12 2c3 3 3 17 0 20" fill="none" stroke="var(--band-mid)" stroke-width="1.5"/></svg>
        www.HarborlineRenewal.example
      </p>
      <p class="tagline"><span class="tagline__lead">Specializing</span> in Water Damage Restoration</p>
    </div>
  </div>
</body>
</html>
```